Telecommunications/Power civil contractor needs business card design

Were a new telecommunications/power underground civil contractor that is looking for a new business card design. Our company colours are silver or grey and orange. Feel free to use the white background logo or the black background logo.

Target Market(s)

Local contractors, utility companies, private sector mining/energy companies, developers.

Industry/Entity Type

Telecommunications

Contact Information for Business Card

Each card will need the following info:
Persons name:
Title:
E-mail:
Phone number:
Shop Address:
Mailing Address:

Requirements
Must have
• Each card will need the following info:
• Persons name:
• Title:
• E-mail:
• Phone number:
• Shop Address:
• Mailing Address:

```html
<!DOCTYPE html>
<html lang="en">
<head>
<meta charset="utf-8">
<title>Ridgeline Conduit Inc – Business Card</title>
<link href="https://fonts.googleapis.com/css2?family=Source+Sans+3:wght@400;600;700&display=swap" rel="stylesheet">
<style>
  :root {
    --orange: #d04f21;
    --grey-text: #5a5a5a;
    --grey-dark: #4d4d4f;
    --rule: #8a8a8a;
    --paper: #f6f6f4;
    --stage: #e4e4e4;
    --white: #ffffff;
  }
  * { margin: 0; padding: 0; box-sizing: border-box; }
  html, body {
    width: 1105px;
    height: 1200px;
    overflow: hidden;
    background: var(--stage);
    font-family: "Source Sans 3", "Myriad Pro", Arial, sans-serif;
  }
  .card {
    position: absolute;
    left: 177px;
    width: 750px;
    height: 428px;
  }
  .card--front { top: 110px; background: var(--paper); }
  .card--back  { top: 660px; background: var(--orange); }

  /* Front */
  .accent-bar {
    position: absolute; left: 0; top: 178px;
    width: 18px; height: 52px; background: var(--orange);
  }
  .person { position: absolute; left: 50px; top: 180px; }
  .person__name { color: var(--orange); font-size: 29px; font-weight: 600; line-height: 1.1; }
  .person__title { color: var(--grey-text); font-size: 21px; line-height: 1.3; }
  .divider {
    position: absolute; left: 50px; top: 248px;
    width: 654px; height: 1px; background: var(--rule);
  }
  .brand { position: absolute; text-align: center; }
  .brand--front { left: 470px; top: 38px; width: 252px; }
  .brand__mark {
    display: block; margin: 0 auto 12px;
    border-radius: 50%;
  }
  .brand--front .brand__mark { width: 100px; height: 100px; border: 6px solid var(--orange); }
  .brand__name {
    font-weight: 700; text-transform: uppercase; letter-spacing: 0.5px; line-height: 1.1;
  }
  .brand--front .brand__name { color: var(--grey-dark); font-size: 25px; }

  .contacts { position: absolute; left: 50px; top: 304px; list-style: none; }
  .contacts li {
    display: flex; align-items: center; gap: 10px;
    height: 29px; color: var(--grey-text); font-size: 20px;
  }
  .contacts svg { width: 17px; height: 17px; fill: var(--orange); flex: none; }
  .address {
    position: absolute; right: 46px; top: 336px;
    text-align: right; color: var(--grey-text); font-size: 20px; line-height: 29px;
    font-style: normal;
  }

  /* Back */
  .brand--back { left: 0; top: 96px; width: 750px; }
  .brand--back .brand__mark { width: 140px; height: 140px; border: 7px solid var(--white); margin-bottom: 18px; }
  .brand--back .brand__name { color: var(--white); font-size: 42px; }
</style>
</head>
<body>
  <section class="card card--front">
    <div class="accent-bar"></div>
    <div class="person">
      <p class="person__name">Dana Whitlock</p>
      <p class="person__title">CEO/Founder</p>
    </div>
    <div class="divider"></div>

    <div class="brand brand--front">
      <span class="brand__mark"></span>
      <p class="brand__name">Ridgeline Conduit Inc</p>
    </div>

    <ul class="contacts">
      <li>
        <svg viewBox="0 0 24 24" aria-hidden="true"><path d="M6.6 10.8a15.1 15.1 0 0 0 6.6 6.6l2.2-2.2a1 1 0 0 1 1-.25 11.4 11.4 0 0 0 3.6.57 1 1 0 0 1 1 1V20a1 1 0 0 1-1 1A17 17 0 0 1 3 4a1 1 0 0 1 1-1h3.5a1 1 0 0 1 1 1c0 1.25.2 2.45.57 3.57a1 1 0 0 1-.25 1z"/></svg>
        555 201 4830
      </li>
      <li>
        <svg viewBox="0 0 24 24" aria-hidden="true"><path d="M2 5h20v14H2z M3 6l9 7 9-7" fill="var(--orange)"/><path d="M3.5 6.5l8.5 6.5 8.5-6.5" fill="none" stroke="#f6f6f4" stroke-width="1.6"/></svg>
        dana@ridgeline.com
      </li>
      <li>
        <svg viewBox="0 0 24 24" aria-hidden="true"><circle cx="12" cy="12" r="10"/><path d="M2 12h20M12 2c3 3 3 17 0 20M12 2c-3 3-3 17 0 20" fill="none" stroke="#f6f6f4" stroke-width="1.4"/></svg>
        www.ridgeline.com
      </li>
    </ul>

    <address class="address">
      1420 Birchwood Road<br>
      Fairbanks, Alaska 99701
    </address>
  </section>

  <section class="card card--back">
    <div class="brand brand--back">
      <span class="brand__mark"></span>
      <p class="brand__name">Ridgeline Conduit Inc</p>
    </div>
  </section>
</body>
</html>
```